ELsewhen website redesign to provide information about experiential workshops, film work and other

We need a redesign of our website elsewhen.org. We conduct experiential workshops of discovery and transformation for individuals and organizations. We need the website to reflect the full extent of ELsewhen programs, and be an information hub for ELsewhen workshops and communities as they develop.

The attached documents contain information about the organization - it's brandbook, copy for web pages, a website layout and a couple of images.

The site is for individuals and companies looking to promote and be change to make a difference. It should be warm, welcoming, and create excitement around the concepts and the ability to discover a new way of being in the world. We are about creating communities around the globe who will embody play, freedom, curiosity and expanded possibilities. We are creating a space for this to happen, both physically (workshops) and online.

We will be on either a SquareSpace, but mos tlikely a Weebly plaform.

Please look at the current site at www.elsewhen.org

Target Market(s)

Initially, are target market will be baby boomers, but will expand to include millennials and students.

Coding

Coded - Design and coding required

Number of Pages Required

5+ page

Requirements
Must have
• The colors, logo and fonts from the brand book.
Nice to have
• Complimentary use of brand colors to create an attractive presentation and energy

```html
<!DOCTYPE html>
<html lang="en">
<head>
<meta charset="utf-8">
<title>ELsewhen — Experiential Workshops</title>
<link href="https://fonts.googleapis.com/css2?family=Jost:wght@300;400;500;600&family=Lato:wght@400;700&display=swap" rel="stylesheet">
<style>
:root{
  --orange:#f15a24;
  --rust:#c1401c;
  --ink:#111111;
  --charcoal:#2a2622;
  --paper:#ffffff;
  --mist:#efefef;
  --grey:#6f6f6f;
  --forest:#2f5a3a;
  --veil:rgba(18,18,18,.74);
}
*{box-sizing:border-box;margin:0;padding:0}
html,body{width:1200px;height:3409px;overflow:hidden}
body{position:relative;font-family:"Jost",sans-serif;color:var(--ink);background:var(--paper)}
section,footer,header{position:absolute;left:0;width:1200px}

/* hero */
.hero{top:0;height:648px;background:linear-gradient(160deg,#4a433c 0%,#2b2724 55%,#1c1a18 100%)}
.brand{position:absolute;top:52px;left:183px;font-weight:600;font-size:31px;letter-spacing:5px;color:var(--paper)}
.brand.small{font-size:22px;letter-spacing:4px}
.login{position:absolute;top:50px;left:820px;width:124px;height:30px;border:1.5px solid var(--paper);border-radius:15px;color:var(--paper);font-size:11px;letter-spacing:1.5px;display:flex;align-items:center;justify-content:center}
.burger{position:absolute;top:54px;left:970px;width:32px}
.burger span{display:block;height:2px;background:var(--paper);margin-bottom:7px}
.hero-rule{position:absolute;top:278px;left:175px;width:44px;height:3px;background:var(--orange)}
.hero-title{position:absolute;top:290px;left:175px;width:870px;font-weight:600;font-size:31px;line-height:38px;color:var(--paper);letter-spacing:.5px}
.hero-title div{display:flex;justify-content:space-between}

/* discover */
.discover{top:648px;height:391px;background:var(--mist);text-align:center}
.discover h2{margin-top:68px;font-weight:600;font-size:22px;line-height:30px;letter-spacing:1px}
.benefits{display:flex;justify-content:center;margin-top:52px}
.benefit{width:170px;color:var(--orange);font-size:11px;font-weight:500;letter-spacing:.5px;line-height:15px}
.benefit svg{display:block;margin:0 auto 14px}

/* vision */
.vision{top:1039px;height:454px;background:linear-gradient(100deg,#6d4030,#8a4b3a 50%,#b04b3d)}
.vision .photo{position:absolute;inset:0}
.vision h2{position:absolute;top:83px;left:648px;color:var(--paper);font-weight:500;font-size:34px;letter-spacing:2px}
.vision p{position:absolute;top:138px;left:648px;width:480px;color:var(--paper);font-size:14px;line-height:26px;font-weight:300}

/* what we do */
.what{top:1493px;height:598px;background:var(--paper);text-align:center}
.what h2{margin-top:85px;font-weight:600;font-size:25px;letter-spacing:1px}
.what h3{margin-top:50px;font-weight:400;font-size:30px}
.what .lead{width:850px;margin:12px auto 0;font-size:13px;line-height:19px;color:var(--grey);font-weight:300}
.what .note{margin-top:60px;color:var(--rust);font-size:22px;line-height:30px}
.moments{display:flex;justify-content:center;gap:40px;margin-top:42px}
.moment{width:150px;font-size:16px;color:var(--charcoal);white-space:nowrap}
.moment svg{display:block;margin:0 auto 10px}

/* screening */
.screening{top:2091px;height:477px;background:linear-gradient(100deg,#a55a1c,#b14e1f 55%,#a13a1b)}
.hex{position:absolute;top:57px;left:141px}
.screening h2{position:absolute;top:90px;left:557px;color:var(--paper);font-weight:400;font-size:30px}
.screening p{position:absolute;left:557px;width:540px;color:var(--paper);font-size:13px;line-height:22px;font-weight:300}

/* community */
.community{top:2568px;height:480px;background:linear-gradient(90deg,#e9e9e9,#f4f4f4 50%,#dcdcdc)}
.community h2{position:absolute;top:132px;left:177px;font-weight:400;font-size:27px}
.community .intro{position:absolute;top:178px;left:177px;width:330px;font-size:16px;line-height:22px;color:var(--grey)}
.contact{position:absolute;top:53px;left:530px;width:486px;height:329px;background:var(--forest);padding:38px 38px 0 38px}
.field{height:33px;background:#e9ece9;margin-bottom:8px;font-size:12px;color:var(--grey);padding:8px 14px}
.field.tall{height:90px}
.send{margin-top:22px;width:110px;height:34px;border-radius:17px;background:var(--ink);color:var(--paper);font-size:13px;letter-spacing:1px;display:flex;align-items:center;justify-content:center}

/* footer */
.site-footer{top:3048px;height:361px;background:#0d0d0d;color:var(--paper)}
.site-footer .brand{top:84px;left:185px}
.col{position:absolute;top:84px}
.col h4{font-weight:400;font-size:15px;letter-spacing:1px;margin-bottom:22px}
.col li{list-style:none;font-size:14px;line-height:32px;color:#cfcfcf}
.socials{display:flex;gap:22px}
.socials span{width:16px;height:16px;border-radius:50%;background:#cfcfcf}
.copyright{position:absolute;top:312px;width:1200px;text-align:center;font-size:11px;color:#777}

/* sign-up overlay */
.veil{position:absolute;top:0;left:0;width:1200px;height:3409px;background:var(--veil)}
.signup{position:absolute;top:173px;left:389px;width:457px;height:357px;background:var(--orange);padding:48px 35px 0 35px;font-family:"Lato",sans-serif}
.signup .line{height:62px;border-bottom:1.5px solid var(--paper);color:var(--paper);font-size:17px;padding:14px 0 0 20px;letter-spacing:.5px}
.signup .line:first-child{height:43px;padding-top:0}
.signup .cta{margin-top:26px;height:64px;background:var(--ink);color:var(--paper);font-weight:700;font-size:21px;display:flex;align-items:center;justify-content:center}
</style>
</head>
<body>

<header class="hero" role="img" aria-label="Dark photograph of a workshop gathering">
  <div class="brand">ELSEWHEN</div>
  <div class="login">MEMBER LOGIN</div>
  <div class="burger"><span></span><span></span><span></span></div>
  <div class="hero-rule"></div>
  <div class="hero-title">
    <div><span>WHAT WORLD DO YOU</span><span>WHAT KIND OF LIFE DO</span></div>
    <div><span>WANT TO LIVE IN?</span><span>YOU WANT TO CREATE?</span></div>
  </div>
</header>

<section class="discover">
  <h2>DISCOVER AN OPPORTUNITY TO LIVE A MORE<br>DYNAMIC AND MEANINGFUL LIFE</h2>
  <div class="benefits">
    <div class="benefit">
      <svg width="54" height="54" viewBox="0 0 54 54" fill="none" stroke="#f15a24" stroke-width="2"><circle cx="27" cy="22" r="12"/><path d="M21 36h12M22 42h10M27 4v4M9 22h4M41 22h4"/></svg>
      MORE<br>ENERGY
    </div>
    <div class="benefit">
      <svg width="54" height="54" viewBox="0 0 54 54" fill="none" stroke="#f15a24" stroke-width="2"><rect x="8" y="6" width="38" height="44"/><path d="M27 6v44M22 28h2M30 28h2"/></svg>
      CREATE OPPORTUNITIES<br>FOR CONNECTING
    </div>
    <div class="benefit">
      <svg width="54" height="54" viewBox="0 0 54 54" fill="none" stroke="#f15a24" stroke-width="2"><circle cx="27" cy="12" r="6"/><circle cx="13" cy="30" r="5"/><circle cx="41" cy="30" r="5"/><path d="M17 50v-8h20v8M4 50v-6h18M32 44h18v6"/></svg>
      EXPLORE<br>CONSCIOUS EVOLUTION
    </div>
    <div class="benefit">
      <svg width="54" height="54" viewBox="0 0 54 54" fill="none" stroke="#f15a24" stroke-width="2"><circle cx="22" cy="12" r="6"/><path d="M22 20v16l-8 14M22 36l8 14M12 26h20l14-14"/></svg>
      EXPAND<br>EXPERIENCE OF LIFE
    </div>
    <div class="benefit">
      <svg width="54" height="54" viewBox="0 0 54 54" fill="none" stroke="#f15a24" stroke-width="2"><circle cx="27" cy="27" r="20"/><ellipse cx="27" cy="27" rx="9" ry="20"/><path d="M7 27h40M11 17h32M11 37h32"/></svg>
      PROVIDE OPPORTUNITIES<br>FOR COLLABORATION<br>AND CREATION
    </div>
  </div>
</section>

<section class="vision">
  <div class="photo" role="img" aria-label="Photograph of workshop participants seated on the floor in a warm room"></div>
  <h2>VISION</h2>
  <p>We envision a world of people living freely and fully, where curiosity and play open the way to new ways of being together. Our workshops invite each person to step beyond old patterns and discover what is possible when communities gather with openness, courage and care, creating a living network of change.</p>
</section>

<section class="what">
  <h2>WHAT WE DO</h2>
  <h3>Elsewhen Life</h3>
  <p class="lead">Elsewhen Life is a workshop designed to engage you with life through new eyes, practices and personal exploration. We call this a journey that gently invites you to look again at the beliefs and patterns that have shaped your world and relationships, as well as a path to transforming the way you live.</p>
  <p class="note">Elsewhen Life is a 2–3 day workshop<br>experienced in 5 movements</p>
  <div class="moments">
    <div class="moment"><svg width="70" height="70" viewBox="0 0 70 70" fill="none" stroke="#c1401c" stroke-width="2"><circle cx="35" cy="35" r="32"/></svg>Curiosity</div>
    <div class="moment"><svg width="70" height="70" viewBox="0 0 70 70" fill="none" stroke="#c1401c" stroke-width="2"><path d="M35 3L67 67H3Z"/><path d="M35 3v64"/></svg>Awareness</div>
    <div class="moment"><svg width="70" height="70" viewBox="0 0 70 70" fill="none" stroke="#c1401c" stroke-width="2"><path d="M2 15l33 20L2 55ZM68 15L35 35l33 20Z"/></svg>Clearing Your Creation</div>
    <div class="moment"><svg width="70" height="70" viewBox="0 0 70 70" fill="none" stroke="#c1401c" stroke-width="2"><path d="M35 2v66M8 15l54 40M62 15L8 55"/></svg>Reimagining</div>
    <div class="moment"><svg width="70" height="70" viewBox="0 0 70 70" fill="none" stroke="#c1401c" stroke-width="2"><path d="M35 3L67 67H3Z"/><path d="M18 37h34M35 37v30"/></svg>Manifesting</div>
  </div>
</section>

<section class="screening">
  <svg class="hex" width="348" height="334" viewBox="0 0 348 334">
    <polygon points="87,2 261,2 346,167 261,332 87,332 2,167" fill="none" stroke="#e3a04e" stroke-width="2"/>
    <polygon points="95,16 253,16 330,167 253,318 95,318 18,167" fill="#5a4a3e" role="img" aria-label="Photograph of a group gathered for an evening session"/>
  </svg>
  <h2>Quiet Bridges</h2>
  <p style="top:145px">Quiet Bridges is our evening program built around short films made by members of the Elsewhen community. Each story follows ordinary people who paused, listened and chose a different way forward in their families, workplaces and neighbourhoods, and invites viewers to see their own lives afresh.</p>
  <p style="top:260px">Every session closes with a guided circle that brings the stories home, giving people space to share what moved them, name what they want to change and imagine together the kind of community they want to build.</p>
</section>

<section class="community" role="img" aria-label="Soft photograph of people in a community gathering">
  <h2>In Your Community</h2>
  <p class="intro">Bring Elsewhen or the Quiet Bridges program to your community. We would love to hear from you. Please fill out the brief form here and let us know.</p>
  <form class="contact">
    <div class="field">Your Name</div>
    <div class="field">Email address</div>
    <div class="field">Phone</div>
    <div class="field tall">Message</div>
    <div class="send">SEND</div>
  </form>
</section>

<footer class="site-footer">
  <div class="brand small">ELSEWHEN</div>
  <div class="col" style="left:393px"><h4>QUICK LINKS</h4><ul><li>About Us</li><li>Workshops</li><li>Elsewhen Friends</li><li>Films</li></ul></div>
  <div class="col" style="left:575px"><h4>RESOURCES</h4><ul><li>Store &amp; Resources</li><li>Community</li><li>Contact Us</li></ul></div>
  <div class="col" style="left:773px"><h4>FOLLOW US</h4><div class="socials"><span></span><span></span><span></span><span></span></div></div>
  <div class="copyright">© 2016 Elsewhen. All rights reserved.</div>
</footer>

<div class="veil"></div>
<form class="signup">
  <div class="line">FIRST NAME</div>
  <div class="line">LAST NAME</div>
  <div class="line">EMAIL ADDRESS</div>
  <div class="cta">SIGN UP NOW</div>
</form>

</body>
</html>
```